Business Card Design for Property Development Company Director

I am looking for a professional and unforgettable business card design for our Director of our Property Development Company.
Please see attached .pptx file to find out what information to include. You don't have to follow the exact format shown in the file - I am interested to see your creative flair using the information provided.

```html
<!DOCTYPE html>
<html lang="en">
<head>
<meta charset="utf-8">
<title>Halvern Property Group – Business Cards</title>
<link rel="stylesheet" href="https://fonts.googleapis.com/css2?family=Roboto:wght@400;500;700&family=Roboto+Condensed:wght@700&display=swap">
<style>
  :root {
    --bg: #e4e5e7;
    --card: #f4f4f5;
    --blue: #24428a;
    --grey: #55585c;
    --text: #4a4d52;
  }
  * { margin: 0; padding: 0; box-sizing: border-box; }
  html, body { width: 1200px; height: 726px; overflow: hidden; }
  body {
    background: var(--bg);
    font-family: "Roboto", Arial, sans-serif;
    position: relative;
  }
  .card {
    position: absolute;
    top: 198px;
    width: 540px;
    height: 330px;
    background: var(--card);
    box-shadow: 0 6px 18px rgba(0,0,0,0.12);
    overflow: hidden;
  }
  .card--front { left: 36px; }
  .card--back { left: 624px; }

  /* front */
  .tagline {
    position: absolute;
    top: 52px; left: 0; right: 0;
    text-align: center;
    color: var(--blue);
    font-size: 20px;
    line-height: 1.2;
    font-weight: 400;
  }
  .front-brand {
    position: absolute;
    top: 134px; left: 0; right: 0;
    display: flex; align-items: center; justify-content: center;
    gap: 16px;
  }
  .brand-square {
    width: 42px; height: 42px;
    background: var(--blue);
  }
  .brand-name {
    color: var(--blue);
    font-weight: 700;
    font-size: 34px;
    letter-spacing: 1px;
    text-transform: uppercase;
  }
  .accent-bar {
    position: absolute;
    top: 204px; left: 0; right: 0;
    height: 8px;
    display: flex;
  }
  .accent-bar .grey { flex: 1; background: var(--grey); }
  .accent-bar .blue { flex: 1; background: var(--blue); }
  .prompt {
    position: absolute;
    top: 238px; left: 0; right: 0;
    text-align: center;
    color: var(--text);
    font-size: 15px;
    letter-spacing: 0.5px;
  }
  .prompt .hl { color: var(--blue); }

  /* back */
  .back-brand {
    position: absolute;
    top: 32px; right: 30px;
    color: var(--blue);
    font-weight: 700;
    font-size: 24px;
    letter-spacing: 1px;
    text-transform: uppercase;
  }
  .decor-circle {
    position: absolute;
    left: -70px; bottom: -90px;
    width: 300px; height: 300px;
    border-radius: 50%;
    background: var(--blue);
  }
  .contact {
    position: absolute;
    top: 84px; right: 30px;
    text-align: right;
    color: var(--text);
    font-size: 14px;
    line-height: 1.55;
  }
  .contact .person {
    font-family: "Roboto Condensed", Arial, sans-serif;
    font-weight: 700;
    color: var(--blue);
    font-size: 20px;
    line-height: 1.2;
  }
  .contact .role { margin-bottom: 10px; }
  .contact .row { display: flex; justify-content: flex-end; align-items: center; gap: 8px; }
  .contact .icon { width: 13px; height: 13px; flex: none; }
  .contact .licence-label { margin-top: 10px; }
  .contact .licence { color: var(--blue); }
</style>
</head>
<body>

<section class="card card--front">
  <p class="tagline">Property Development<br>&amp; Site Acquisition Specialists</p>
  <div class="front-brand">
    <span class="brand-square"></span>
    <span class="brand-name">Halvern Property Group</span>
  </div>
  <div class="accent-bar"><span class="grey"></span><span class="blue"></span></div>
  <p class="prompt">Ask me about our <span class="hl">INVESTMENT &amp; PARTNERSHIP</span> opportunities</p>
</section>

<section class="card card--back">
  <span class="decor-circle"></span>
  <div class="back-brand">Halvern Property Group</div>
  <div class="contact">
    <p class="person">Daniel Marsh</p>
    <p class="role">Director</p>
    <p class="row">0412 308 615
      <svg class="icon" viewBox="0 0 16 16"><path d="M4 1l3 3-2 2c1 2 3 4 5 5l2-2 3 3-2 3C7 15 1 9 1 3z" fill="#24428a"/></svg>
    </p>
    <p class="row">daniel@halvern.com.au
      <svg class="icon" viewBox="0 0 16 16"><rect x="1" y="3" width="14" height="10" fill="#24428a"/><path d="M1 3l7 6 7-6" fill="none" stroke="#f4f4f5" stroke-width="1.4"/></svg>
    </p>
    <p class="row">www.halvern.com.au
      <svg class="icon" viewBox="0 0 16 16"><circle cx="8" cy="8" r="6.5" fill="none" stroke="#24428a" stroke-width="1.5"/><path d="M1.5 8h13M8 1.5c-3 3.5-3 9.5 0 13M8 1.5c3 3.5 3 9.5 0 13" fill="none" stroke="#24428a" stroke-width="1.2"/></svg>
    </p>
    <p class="licence-label">Real Estate Lic:</p>
    <p class="licence">5519203 &amp; 5519204</p>
  </div>
</section>

</body>
</html>
```